Summit Ridge Business Card

Side 1: Summit Ridge Logo (logo without Maltese cross) with industrial rope rescue related theme. Our company services - TRAINING - Fire Training, Confined Space Rescue Training, Rope Rescue training, Hazmat Training, Incident Command, EMS, Pump Operations Training. Website - summitridgeexample.com.
Side 2: Summit Ridge Fire Department Logo (logo with Maltese cross) with Firefighter related theme. Company (division) services - FIELD SERVICES - Fire Department, Stand-by Rescue, Safety, EMS, Planning. "Supporting the Emergency Response Community Since 1967"

Add contact information wherever it makes since (Name, Email, Phone).
I would like it to represent the Summit Ridge Fire Department Logo as a division not as a separate entity without saying it, possibly by depicting it in the background of Side 2 instead of being a standalone picture like the logo on Side 1.

```html
<!DOCTYPE html>
<html lang="en">
<head>
<meta charset="utf-8">
<title>Summit Ridge Business Card</title>
<link rel="stylesheet" href="https://fonts.googleapis.com/css2?family=Poppins:wght@400;500;600;700;800&display=swap">
<style>
  :root {
    --stage: #2b2b2b;
    --card-dark: #1b1b1b;
    --card-light: #ffffff;
    --red: #e8281e;
    --ink: #111111;
    --text-light: #f2f2f2;
    --rule: #222222;
  }
  * { box-sizing: border-box; margin: 0; padding: 0; }
  html, body { width: 1200px; height: 866px; overflow: hidden; }
  body {
    background: var(--stage);
    font-family: "Poppins", sans-serif;
    display: flex;
    flex-direction: column;
    align-items: center;
    justify-content: center;
    gap: 40px;
  }
  .card {
    position: relative;
    width: 640px;
    height: 366px;
    overflow: hidden;
    box-shadow: 0 14px 30px rgba(0,0,0,.45);
  }

  /* Side 1 */
  .card--front { background: var(--card-dark); color: var(--text-light); }
  .service-list { position: absolute; left: 44px; top: 52px; }
  .service-list__title {
    color: var(--red); font-weight: 700; font-size: 20px; letter-spacing: .5px; margin-bottom: 8px;
  }
  .service-list ul { list-style: none; }
  .service-list li {
    position: relative; padding-left: 16px; font-size: 13.5px; font-weight: 500;
    line-height: 1.72; text-transform: uppercase;
  }
  .service-list li::before {
    content: ""; position: absolute; left: 0; top: 9px; width: 7px; height: 7px;
    border-radius: 50%; background: var(--red);
  }
  .brand {
    position: absolute; right: 40px; top: 112px; width: 250px; text-align: center;
  }
  .brand__name {
    display: flex; align-items: center; justify-content: center; gap: 10px;
    font-size: 30px; font-weight: 800; color: var(--red); letter-spacing: 1px; text-transform: uppercase;
  }
  .brand__mark { width: 18px; height: 18px; background: var(--red); flex: none; }
  .brand__rule { display: flex; gap: 8px; margin-top: 10px; }
  .brand__rule span { height: 3px; background: var(--red); flex: 1; }
  .website {
    position: absolute; right: 44px; bottom: 36px; font-size: 15px; color: var(--text-light);
  }
  .website em { font-style: normal; color: var(--red); }

  /* Side 2 */
  .card--back { background: var(--card-light); color: var(--ink); }
  .card--back .service-list { top: 42px; }
  .card--back .service-list li { color: var(--ink); }
  .divider {
    position: absolute; left: 44px; right: 44px; top: 212px; height: 1px; background: var(--rule);
  }
  .tagline {
    position: absolute; left: 44px; top: 226px; color: var(--red); font-size: 14px; font-weight: 500;
  }
  .contact { position: absolute; right: 44px; top: 62px; text-align: left; }
  .contact__name { font-size: 24px; font-weight: 700; letter-spacing: .5px; margin-bottom: 6px; }
  .contact__line { display: flex; align-items: center; gap: 8px; font-size: 15px; line-height: 1.6; }
  .contact__line svg { width: 14px; height: 14px; flex: none; }
  .base-band { position: absolute; left: 0; bottom: 0; width: 100%; height: 70px; }
</style>
</head>
<body>

  <section class="card card--front" aria-label="Business card side one">
    <div class="service-list">
      <h2 class="service-list__title">TRAINING</h2>
      <ul>
        <li>Fire Training</li>
        <li>Rope Rescue Training</li>
        <li>Hazmat Training</li>
        <li>Confined Space Rescue Training</li>
        <li>Incident Command</li>
        <li>EMS</li>
        <li>Pump Operations Training</li>
      </ul>
    </div>
    <div class="brand">
      <div class="brand__name"><span class="brand__mark"></span>Summit Ridge</div>
      <div class="brand__rule"><span></span><span></span></div>
    </div>
    <p class="website">www.<em>summitridgeexample</em>.com</p>
  </section>

  <section class="card card--back" aria-label="Business card side two">
    <div class="service-list">
      <h2 class="service-list__title">FIELD SERVICES</h2>
      <ul>
        <li>Fire Department</li>
        <li>Stand-by Rescue</li>
        <li>Safety</li>
        <li>EMS</li>
        <li>Planning</li>
      </ul>
    </div>
    <div class="contact">
      <p class="contact__name">Daniel Moreno</p>
      <p class="contact__line">
        <svg viewBox="0 0 24 24" aria-hidden="true"><path fill="#e8281e" d="M6.6 10.8a15.5 15.5 0 0 0 6.6 6.6l2.2-2.2a1 1 0 0 1 1-.25 11.4 11.4 0 0 0 3.6.57 1 1 0 0 1 1 1V20a1 1 0 0 1-1 1A17 17 0 0 1 3 4a1 1 0 0 1 1-1h3.5a1 1 0 0 1 1 1c0 1.25.2 2.45.57 3.6a1 1 0 0 1-.25 1z"/></svg>
        044-555 010 220
      </p>
      <p class="contact__line">
        <svg viewBox="0 0 24 24" aria-hidden="true"><path fill="#e8281e" d="M2 5h20v14H2z"/><path fill="none" stroke="#fff" stroke-width="1.6" d="M2.5 5.5 12 13l9.5-7.5"/></svg>
        info@mailexample.com
      </p>
    </div>
    <div class="divider"></div>
    <p class="tagline">Supporting the Emergency Response Community Since 1967</p>
    <svg class="base-band" viewBox="0 0 640 70" preserveAspectRatio="none" aria-hidden="true">
      <path d="M0 40 L300 66 L330 66 C360 50 380 44 420 44 L640 44 L640 70 L0 70 Z" fill="#1b1b1b"/>
      <path d="M0 30 L300 60 L300 66 L0 40 Z" fill="#e8281e"/>
    </svg>
  </section>

</body>
</html>
```